Meridian Vault Data Works Needs a Website Desing

We need a website design for a new company based in Kuwait called Meridian Vault Data Works (MVDW). We provide Software as a Service (SaaS) solutions for small and medium business companies. We will develop the required E-systems like HR,Payroll,Accounting Systems for those customers who wants to focus on their business instead of wasting time to automate it. MVDW need a web site that represent this activity and showing our cloud products and allow out customers to easily identify their needs. as a normal web site basic things need to be included like :
about MVDW
Solutions
PressRoom
Contact us
please i need something similar to tralvex.com or ozk.com or www.plorvane.com with blue and black theme .. please check the Company's logo
hi all ,,,
the project is only design without any codes
Reason: The project is focus on design only ,, i will be really appreciated to have more designs

```html
<!DOCTYPE html>
<html lang="en">
<head>
<meta charset="utf-8">
<title>Meridian Vault Data Works</title>
<link href="https://fonts.googleapis.com/css2?family=Ubuntu:wght@400;500;700&family=Noto+Sans:wght@400;700&display=swap" rel="stylesheet">
<style>
:root{
  --blue:#1a86c8;
  --blue-light:#3aa6e6;
  --blue-dark:#0f6aa8;
  --ink:#333;
  --muted:#666;
  --dark:#1c1c1c;
  --darker:#111;
  --band:#eeeff1;
  --line:#d4d6d9;
  --white:#fff;
  --placeholder:#b4b8a6;
}
*{margin:0;padding:0;box-sizing:border-box}
html,body{width:1200px;height:1155px;overflow:hidden}
body{position:relative;font-family:"Noto Sans",Tahoma,sans-serif;color:var(--ink);background:var(--white)}
h1,h2,h3{font-weight:400}
.abs{position:absolute}
.topbar{left:0;top:0;width:1200px;height:72px;background:linear-gradient(#2a2a2a,#1a1a1a)}
.topbar .contact-line{left:125px;top:12px;color:var(--white);font-size:13.5px}
.btn{display:inline-block;background:linear-gradient(var(--blue-light),var(--blue-dark));color:var(--white);border-radius:4px;text-align:center;font-size:13px;box-shadow:inset 0 1px 0 rgba(255,255,255,.35)}
.btn-login{left:922px;top:9px;width:71px;height:25px;line-height:25px;font-size:14.5px}
.btn-register{left:1001px;top:9px;width:73px;height:25px;line-height:25px;font-size:14.5px}
.hero{left:0;top:72px;width:1200px;height:428px;background:var(--placeholder)}
.header{left:106px;top:44px;width:989px;height:72px;background:var(--white);border-radius:4px;box-shadow:0 2px 8px rgba(0,0,0,.35);z-index:2}
.brand{left:22px;top:14px;display:flex;align-items:center;gap:10px}
.brand .mark{width:44px;height:44px;border-radius:50%;background:var(--blue)}
.brand .name{font-family:"Ubuntu",sans-serif;font-weight:700;font-size:40px;color:#1f1f1f;letter-spacing:1px}
.nav{top:27px;font-size:14px;color:#444}
.nav.active{color:var(--blue);border-bottom:1px solid var(--blue)}
.nav-sep{top:29px;width:1px;height:14px;background:#bbb}
.arrow{width:42px;height:42px;border-radius:50%;background:rgba(30,30,30,.8);top:265px;z-index:2}
.hero-title{left:505px;top:256px;font-family:"Ubuntu",sans-serif;font-weight:500;font-size:25px;color:var(--blue);z-index:2}
.hero-text{left:505px;top:294px;width:490px;font-size:17px;line-height:24px;color:#333;z-index:2}
.rule{left:0;top:500px;width:1200px;height:4px;background:var(--blue)}
.band{left:0;top:504px;width:1200px;height:111px;background:var(--band)}
.cell{top:504px;width:160px;height:111px;text-align:center}
.cell svg{position:absolute;left:53px;top:12px}
.cell .label{position:absolute;left:0;width:100%;top:76px;font-size:14.5px;color:#333}
.cell.active .label{top:79px;color:#111}
.cell.active{background:#f7f8f9}
.pointer{left:986px;top:504px;width:0;height:0;border-left:14px solid transparent;border-right:14px solid transparent;border-top:10px solid var(--blue)}
.vsep{top:510px;width:1px;height:96px;background:var(--line)}
.col-title{top:648px;font-family:"Ubuntu",sans-serif;font-size:21px;color:#333}
.body-text{font-size:12px;line-height:20px;color:var(--muted)}
.about-text{left:125px;top:682px;width:305px}
.list{list-style:none}
.list li{position:relative;padding-left:22px;font-size:12px;line-height:23.8px;color:var(--muted)}
.list li::before{content:"";position:absolute;left:2px;top:11px;width:8px;height:2px;background:var(--blue)}
.list li::after{content:"";position:absolute;left:6px;top:8px;border-left:5px solid var(--blue);border-top:4px solid transparent;border-bottom:4px solid transparent}
.benefits{left:474px;top:681px}
.reasons{left:785px;top:681px}
.btn-more{top:857px;width:76px;height:28px;line-height:28px;font-size:12.5px}
.dash{top:654px;height:233px;border-left:1px dashed #bbb}
.footer{left:0;top:924px;width:1200px;height:191px;background:var(--dark)}
.foot-title{top:941px;font-family:"Ubuntu",sans-serif;font-size:17px;color:var(--white)}
.foot-list{list-style:none}
.foot-list li{position:relative;padding-left:22px;font-size:12.5px;line-height:27px;color:#9dcff0}
.foot-list li::before{content:"";position:absolute;left:0;top:13px;width:8px;height:2px;background:var(--blue-light)}
.foot-list li::after{content:"";position:absolute;left:4px;top:10px;border-left:5px solid var(--blue-light);border-top:4px solid transparent;border-bottom:4px solid transparent}
.fsep{top:940px;width:1px;height:160px;background:#2e2e2e}
.news-text{left:581px;top:974px;width:230px;font-size:12px;line-height:19px;color:#cfe6f6}
.email-field{left:581px;top:1018px;width:209px;height:27px;background:#5a5a5a;border-radius:3px;color:#aaa;font-size:12px;line-height:27px;padding-left:16px}
.btn-signup{left:582px;top:1057px;width:75px;height:26px;line-height:26px;font-size:13.5px}
.contact-row{left:906px;font-size:12.5px;color:var(--white);display:flex;align-items:center;gap:14px}
.social{top:1067px;width:30px;height:30px;border-radius:50%;background:var(--blue)}
.bottom{left:0;top:1115px;width:1200px;height:40px;background:var(--darker);font-size:12.5px;color:var(--white)}
.bottom .privacy{left:125px;top:11px}
.bottom .copy{right:125px;top:11px}
</style>
</head>
<body>

<div class="abs topbar">
  <div class="abs contact-line">Call us: (000) 000-0000 &nbsp; Email: info@mvdwmail.com</div>
  <a class="abs btn btn-login">Login</a>
  <a class="abs btn btn-register">Register</a>
</div>

<div class="abs hero" role="img" aria-label="Hero photograph: a person with raised arms in an open field at sunrise"></div>

<header class="abs header">
  <div class="abs brand"><span class="mark"></span><span class="name">MVDW</span></div>
  <span class="abs nav active" style="left:505px">Home</span>
  <span class="abs nav-sep" style="left:566px"></span>
  <span class="abs nav" style="left:588px">About Us</span>
  <span class="abs nav-sep" style="left:670px"></span>
  <span class="abs nav" style="left:692px">Solutions</span>
  <span class="abs nav-sep" style="left:775px"></span>
  <span class="abs nav" style="left:797px">Services</span>
  <span class="abs nav-sep" style="left:875px"></span>
  <span class="abs nav" style="left:897px">Contact Us</span>
</header>

<div class="abs arrow" style="left:83px">
  <svg width="42" height="42" viewBox="0 0 42 42"><path d="M24 13 L16 21 L24 29" fill="none" stroke="#fff" stroke-width="3.5" stroke-linecap="round" stroke-linejoin="round"/></svg>
</div>
<div class="abs arrow" style="left:1075px">
  <svg width="42" height="42" viewBox="0 0 42 42"><path d="M18 13 L26 21 L18 29" fill="none" stroke="#fff" stroke-width="3.5" stroke-linecap="round" stroke-linejoin="round"/></svg>
</div>
<h1 class="abs hero-title">Meridian Vault Data Works</h1>
<p class="abs hero-text">We provide Software as a Service (SaaS) solutions for small and medium business companies.</p>

<div class="abs rule"></div>
<div class="abs band"></div>

<div class="abs cell" style="left:121px">
  <svg width="54" height="58" viewBox="0 0 54 58"><path d="M27 4a17 17 0 0 0-10 31v7h20v-7A17 17 0 0 0 27 4z" fill="none" stroke="#999" stroke-width="3"/><rect x="19" y="45" width="16" height="4" fill="#999"/><rect x="22" y="51" width="10" height="4" rx="2" fill="#999"/><path d="M20 21h5v10h-5zM26 31v-9l4-7c2 0 3 1 2 4l-1 3h5c2 0 2 2 1 3l-2 6h-9z" fill="var(--blue)"/></svg>
  <div class="label">Software solutions</div>
</div>
<div class="abs vsep" style="left:280px"></div>
<div class="abs cell" style="left:283px">
  <svg width="54" height="58" viewBox="0 0 54 58"><circle cx="27" cy="17" r="11" fill="#999"/><path d="M6 56c0-14 9-22 21-22s21 8 21 22z" fill="#999"/><path d="M25 36h4l-1 20h-2z" fill="var(--blue)"/></svg>
  <div class="label">HR Payroll</div>
</div>
<div class="abs vsep" style="left:440px"></div>
<div class="abs cell" style="left:443px">
  <svg width="54" height="58" viewBox="0 0 54 58"><circle cx="27" cy="29" r="23" fill="none" stroke="#999" stroke-width="5"/><path d="M6 25h42l-10 8h-22z" fill="#999"/><path d="M22 27h10l-5 8z" fill="var(--blue)"/><rect x="24" y="34" width="6" height="16" fill="#999"/></svg>
  <div class="label">Consumer Auto</div>
</div>
<div class="abs vsep" style="left:600px"></div>
<div class="abs cell" style="left:604px">
  <svg width="54" height="58" viewBox="0 0 54 58"><path d="M27 50C8 36 2 28 2 18A12 12 0 0 1 27 12a12 12 0 0 1 25 6c0 10-6 18-25 32z" fill="#999"/><path d="M4 28h14l4-8 5 16 5-12 3 4h15" fill="none" stroke="var(--blue)" stroke-width="2.5" stroke-linejoin="round"/></svg>
  <div class="label">Healthcare</div>
</div>
<div class="abs vsep" style="left:760px"></div>
<div class="abs cell" style="left:764px">
  <svg width="54" height="58" viewBox="0 0 54 58"><rect x="8" y="4" width="38" height="50" rx="5" fill="none" stroke="#999" stroke-width="4"/><rect x="15" y="11" width="24" height="8" fill="var(--blue)"/><g fill="var(--blue)"><rect x="15" y="24" width="6" height="5"/><rect x="24" y="24" width="6" height="5"/><rect x="33" y="24" width="6" height="5"/><rect x="15" y="32" width="6" height="5"/><rect x="24" y="32" width="6" height="5"/><rect x="33" y="32" width="6" height="5"/><rect x="15" y="40" width="6" height="5"/><rect x="24" y="40" width="6" height="5"/><rect x="33" y="40" width="6" height="5"/></g></svg>
  <div class="label">Accounting</div>
</div>
<div class="abs vsep" style="left:920px"></div>
<div class="abs cell active" style="left:921px;width:160px">
  <svg width="70" height="58" viewBox="0 0 70 58" style="left:45px"><path d="M35 29c-8-10-12-14-19-14a14 14 0 0 0 0 28c7 0 11-4 19-14s12-14 19-14a14 14 0 0 1 0 28c-7 0-11-4-19-14z" fill="none" stroke="var(--blue)" stroke-width="6"/></svg>
  <div class="label">Solutions For All</div>
</div>
<div class="abs pointer"></div>

<h2 class="abs col-title" style="left:125px">What is MVDW?</h2>
<p class="abs body-text about-text">Lorem ipsum dolor sit amet, consectetur adipisicing elit esed do eiusmod tempor incididunt ut labore et dolore magna aliqua. Ut enim ad minim veniam, quis nostrud exercitation ullamco laboris nisi ut aliqup ex ea commo esed do eiusmod tempor incididunt ut labore et dolore magna aliqua. Ut enim ad minim veniam, quis nostrud exercitation ullamco laboris nisi ut aliqup ex ea commo voluptate velit esse cillum</p>
<a class="abs btn btn-more" style="left:126px">Read More</a>

<div class="abs dash" style="left:445px"></div>

<h2 class="abs col-title" style="left:474px">Benefits Using SaaS</h2>
<ul class="abs list benefits">
  <li>Affordable</li>
  <li>Quick to Deploy</li>
  <li>Zero Infrastructure</li>
  <li>Seamless Upgrades</li>
  <li>Guaranteed Levels of Service</li>
  <li>Backups and Data Recovery all done for you</li>
  <li>Work Anywhere</li>
</ul>
<a class="abs btn btn-more" style="left:475px">Read More</a>

<div class="abs dash" style="left:760px"></div>

<h2 class="abs col-title" style="left:785px">Why Choose MVDW?</h2>
<ul class="abs list reasons">
  <li>Lorem ipsum dolor sit amet, consectetur adipisicing</li>
  <li>Lorem ipsum dolor sit amet, consectetur adipisicing</li>
  <li>Lorem ipsum dolor sit amet, consectetur adipisicing</li>
  <li>Lorem ipsum dolor sit amet, consectetur adipisicing</li>
  <li>Lorem ipsum dolor sit amet, consectetur adipisicing</li>
  <li>Lorem ipsum dolor sit amet, consectetur adipisicing</li>
  <li>Lorem ipsum dolor sit amet, consectetur adipisicing</li>
</ul>
<a class="abs btn btn-more" style="left:786px">Read More</a>

<footer class="abs footer"></footer>
<h3 class="abs foot-title" style="left:125px">Usefull Links</h3>
<ul class="abs foot-list" style="left:125px;top:969px">
  <li>Home</li><li>About Us</li><li>Solutions</li><li>Contact Us</li>
</ul>
<div class="abs fsep" style="left:280px"></div>
<h3 class="abs foot-title" style="left:336px">Services</h3>
<ul class="abs foot-list" style="left:336px;top:969px">
  <li>Lorem Ipsum Dolor</li><li>Lorem Ipsum Dolor</li><li>Lorem Ipsum Dolor</li><li>Lorem Ipsum Dolor</li><li>Lorem Ipsum Dolor</li>
</ul>
<div class="abs fsep" style="left:524px"></div>
<h3 class="abs foot-title" style="left:581px">Newsletter</h3>
<p class="abs news-text">Lorem ipsum dolor sit amet, consectetur adipisicing elit, sed do.</p>
<div class="abs email-field">Enter Your Email</div>
<a class="abs btn btn-signup">Signup</a>
<div class="abs fsep" style="left:851px"></div>
<h3 class="abs foot-title" style="left:906px">Contact Us</h3>
<div class="abs contact-row" style="top:975px">
  <svg width="12" height="18" viewBox="0 0 12 18"><rect x="1" y="1" width="10" height="16" rx="2" fill="none" stroke="var(--blue-light)" stroke-width="2"/><rect x="4" y="13" width="4" height="2" fill="var(--blue-light)"/></svg>
  <span>(000) 000 0000</span>
</div>
<div class="abs contact-row" style="top:1001px">
  <svg width="16" height="14" viewBox="0 0 16 14"><rect x="1" y="2" width="14" height="11" fill="none" stroke="var(--blue-light)" stroke-width="2"/><path d="M1 3l7 6 7-6" fill="none" stroke="var(--blue-light)" stroke-width="2"/></svg>
  <span>info@mvdwmail.com</span>
</div>
<h3 class="abs foot-title" style="left:906px;top:1040px">Show Some Love</h3>
<span class="abs social" style="left:905px"></span>
<span class="abs social" style="left:944px"></span>
<span class="abs social" style="left:983px"></span>

<div class="abs bottom">
  <span class="abs privacy">Privacy Policy</span>
  <span class="abs copy">Copyright 2013</span>
</div>

</body>
</html>
```